AMBER AND SLATE WEB

We need a home design in wordpress, we have now a web but we would like to improve it. Our current web is www.amberandslatevillas.example Our business is holliday rental of villas in Ibiza. Our guest must know that we are a reliable company, professional and with experience and good reviews. We want them to click in our reservation engine: https://bookings.amberandslatevillas.example/en/ and make reservation in our website. We would also like to say that all the properties that we have are just us who commercialize so we have best price available. Many people are going to see our villas in staylist.example and look to our website to make a reservation with us so we need to show them that they are at the right place and click at our link to our reservation engine. What make us special is that we are a local company, we are from Ibiza, Our guests are always received in person by the Amber and Slate Ibiza team. You will enjoy extensive tourist information when you check in and during the entire stay. You will be attended by ChatterLine and calls, always happy to help so that you have a happy and fun stay! Our guest stay is better than in hotel as they have more spece, private swiming pool, private garden, barbeque ... To rent a villa is the best way to stay in Ibiza. We also have a promotional video: https://vidshare.example/Qm7TzR2pLxA Let our philosophy be shown, we think that coming on holiday to Ibiza implies seeing the nature that we have in Ibiza, hence our name AMBER AND SLATE, like the pins that almost touch the sea in Ibiza, or the posidonea meadows where the intense green of the seaweed and the blue of the sea. We are aware of the environment, and we love Ibiza. For us, the client who visits Ibiza, should rent a car, go around the island, eat in a restaurant one day in front of the sea, is a night of partying to the discs, go shopping, visit the ancient heritage of Umanity, make some aquatic sport, enjoy the pool, those are for us Ibiza.

Target Market(s)

Europe, people from Holand, UK, Germany, France, Spain ...

Industry/Entity Type

Tourism

Colors

Designer to choose colors to be used in the design.

Requirements
Must have
• Pictures of Ibiza.
Nice to have
• Our name Amber and Slate Ibiza is beacuse in Ibiza there is forest that almost touch the watter of the Mediterranean sea, so you can see green of the forest and blue of the sea and the sky. And also beacause under the watter of the sea there is a plant called Posidonia that is also green please see the picture of posidonia.

```html
<!DOCTYPE html>
<html lang="en">
<head>
<meta charset="utf-8">
<title>Amber and Slate Villas Ibiza</title>
<link rel="stylesheet" href="https://fonts.googleapis.com/css2?family=Oswald:wght@500;600&family=Ubuntu:wght@400;500;700&family=Montserrat:wght@300;400;600&display=swap">
<style>
:root{
  --teal:#3fd6b0;
  --ink:#3a3a3a;
  --text:#5b5b5b;
  --white:#ffffff;
  --sea-deep:#0f58b8;
  --sea-light:#2fc4e0;
  --pine:#2f6b2a;
  --sand:#e9d4a8;
  --btn-dark:rgba(4,36,46,.85);
  --soft:#fafafa;
  --nav-blue:#1a7fd6;
}
*{margin:0;padding:0;box-sizing:border-box}
html,body{width:1200px;height:2415px;overflow:hidden;background:var(--white)}
body{position:relative;font-family:'Montserrat',sans-serif;color:var(--text)}
.abs{position:absolute}

/* hero */
.hero{left:0;top:0;width:1200px;height:675px;
  background:
    radial-gradient(ellipse 380px 260px at 120px 560px,#3f7a2c 0%,rgba(63,122,44,0) 100%),
    radial-gradient(ellipse 420px 300px at 1080px 260px,#3c6f2d 0%,rgba(60,111,45,0) 100%),
    radial-gradient(ellipse 360px 220px at 900px 560px,var(--sand) 0%,rgba(233,212,168,0) 100%),
    radial-gradient(ellipse 420px 200px at 560px 470px,#48d6e4 0%,rgba(72,214,228,0) 100%),
    linear-gradient(180deg,#1d7fe0 0%,#0e56b6 30%,#0c4fa8 45%,#1a8fd0 70%,#38c6d6 100%);}
.brand{left:89px;top:54px;display:flex;align-items:center;gap:8px;color:var(--white);font-family:'Ubuntu',sans-serif;font-weight:400;font-size:17px;letter-spacing:.5px}
.brand-dot{width:24px;height:24px;border-radius:50%;background:var(--white)}
.nav{top:58px;left:485px;display:flex;align-items:center;gap:0;font-family:'Montserrat',sans-serif;font-weight:600;font-size:10px;color:var(--white)}
.nav a{color:inherit;text-decoration:none;margin-right:23px;line-height:18px}
.nav .nav-outline{border:1.5px solid var(--white);padding:0 5px;margin-left:0}
.nav .nav-solid{background:var(--white);color:var(--nav-blue);padding:0 6px}
.hero-title{left:0;top:412px;width:1200px;text-align:center;font-family:'Oswald',sans-serif;font-weight:600;font-size:50px;letter-spacing:1.5px;color:var(--white)}
.hero-btn{left:506px;top:528px;width:188px;height:63px;border:4px solid var(--white);display:flex;align-items:center;justify-content:center;font-family:'Oswald',sans-serif;font-weight:500;font-size:23px;letter-spacing:1px;color:var(--white)}

/* section headings */
.section-title{left:0;width:1200px;display:flex;justify-content:center;align-items:center;font-family:'Ubuntu',sans-serif;font-weight:500;font-size:18px;color:var(--ink);letter-spacing:.5px}
.section-title::before,.section-title::after{content:"";width:49px;height:2px;background:var(--teal);margin:0 34px}

.about-lead{left:230px;top:798px;width:740px;text-align:center;font-size:11.5px;line-height:15px;font-weight:400}
.about-lead strong{color:var(--teal);font-weight:600}
.about-body{left:92px;top:888px;width:500px;font-size:11.5px;line-height:15px;font-weight:400}
.about-body p{margin-bottom:15px}
.photo-stack-back{left:739px;top:909px;width:353px;height:228px;background:var(--white);box-shadow:0 4px 14px rgba(0,0,0,.12)}
.photo-stack-mid{left:725px;top:885px;width:350px;height:235px;background:var(--white);box-shadow:0 4px 14px rgba(0,0,0,.12)}
.about-photo{left:712px;top:876px;width:348px;height:230px;background:linear-gradient(180deg,#7aa6c8 0%,#e8d6a0 38%,#5d8aa0 48%,#a5865a 72%,#6f5a3a 100%)}

/* deals */
.deal{border-radius:8px;overflow:hidden}
.deal-name{position:absolute;left:0;right:0;top:28px;text-align:center;font-family:'Ubuntu',sans-serif;font-weight:500;font-size:16.5px;line-height:19px;color:var(--white);text-shadow:0 1px 3px rgba(0,0,0,.35)}
.deal-btn{position:absolute;width:135px;height:37px;border-radius:5px;background:var(--btn-dark);display:flex;align-items:center;justify-content:center;font-family:'Ubuntu',sans-serif;font-weight:700;font-size:17px;color:#c9b79a}
.deal-btn.teal{color:var(--teal)}
.deal-1{left:87px;top:1268px;width:252px;height:407px;background:linear-gradient(180deg,#2a78d8 0%,#4d8fd6 22%,#e3b23a 40%,#d99a2a 62%,#2aa5d8 80%,#1a7fc8 100%)}
.deal-2{left:346px;top:1268px;width:446px;height:185px;background:linear-gradient(180deg,#6f9a5a 0%,#d8c8b0 35%,#2fb7ec 60%,#c76a45 100%)}
.deal-3{left:799px;top:1268px;width:312px;height:185px;background:linear-gradient(180deg,#1e78e4 0%,#5aa3e8 40%,#6e8a60 65%,#d9d9d9 100%)}
.deal-4{left:346px;top:1460px;width:338px;height:215px;background:linear-gradient(180deg,#a56a3e 0%,#e8e0d2 30%,#efe6d6 70%,#8a6a4a 100%)}
.deal-5{left:691px;top:1460px;width:420px;height:215px;background:linear-gradient(180deg,#2a78dc 0%,#5b9ee4 40%,#eeeeee 62%,#5d7f3a 100%)}

/* testimonials */
.testi-band{left:0;top:1752px;width:1200px;height:318px;background:var(--soft)}
.testi-card{left:335px;top:1822px;width:532px;height:247px;border-radius:16px;background:var(--white);box-shadow:0 2px 14px rgba(0,0,0,.06)}
.avatar{left:562px;top:1851px;width:76px;height:76px;border-radius:50%;background:linear-gradient(180deg,#d7dfe6,#8fb0c8)}
.testi-text{left:420px;top:1961px;width:360px;text-align:center;font-size:13.5px;line-height:17px;color:#555}
.testi-name{left:455px;top:2022px;font-family:'Ubuntu',sans-serif;font-size:13.5px;color:var(--ink)}

/* footer */
.footer{left:0;top:2133px;width:1200px;height:282px;background:
  linear-gradient(180deg,#0f4f8e 0%,#12609a 35%,#2a7f5a 70%,#3c8a2e 100%)}
.foot-col{color:var(--white);font-family:'Montserrat',sans-serif;font-size:11.5px;line-height:15px}
.foot-head{position:absolute;font-family:'Ubuntu',sans-serif;font-weight:500;font-size:13px;color:var(--white);padding-bottom:5px;border-bottom:2px solid var(--white);transform:translateX(-50%)}
.foot-menu{left:912px;top:2220px;width:200px;text-align:center;font-weight:600;font-size:11px;line-height:30px;color:var(--white);letter-spacing:.5px}
</style>
</head>
<body>

<div class="abs hero" role="img" aria-label="Photo of a turquoise Ibiza cove with pine-covered cliffs, sandy beach and anchored sailboats"></div>
<div class="abs brand"><span class="brand-dot"></span>AMBER AND SLATE</div>
<nav class="abs nav">
  <a>HOME</a><a>EXPERIENCE</a><a>ABOUT US</a><a>CONTACT US</a>
  <a class="nav-outline">ALL PROPERTIES</a><a class="nav-solid">BOOK NOW</a>
</nav>
<h1 class="abs hero-title">THE BEST WAY TO STAY IN IBIZA!</h1>
<div class="abs hero-btn">BOOK NOW</div>

<h2 class="abs section-title" style="top:732px">ABOUT US</h2>
<p class="abs about-lead"><strong>Amber and Slate Villas Ibiza</strong> is a company specialized in offering its clients accommodation in Villas on the countryside of Ibiza. Our guests enjoy the rural Ibiza, tranquility, relax, private pool, close to dream beaches and coves, the best restaurants, an unforgettable holiday for family or friends.</p>
<div class="abs about-body">
  <p>Every day can be a different experience, beach, restaurant, flea market, disco, hiking, kayaking, horseback riding, shopping, history, boat ride! There is a lot of variety for all budgets!</p>
  <p>The maximum distances of the island are 41 kilometers from north to south and 15 kilometers from east to west, we always recommend renting a car. Enjoy the freedom to go where you prefer, without depending on schedules or public transportation.</p>
  <p>Each client is different, both for those who discover Ibiza for the first time and for those who have already been many times, it is a pleasure for us to share our favorite places with our guests and help them to make their experience very special.</p>
</div>
<div class="abs photo-stack-back"></div>
<div class="abs photo-stack-mid"></div>
<div class="abs about-photo" role="img" aria-label="Photo of an Ibiza beach at sunset with an islet offshore and palms in the foreground"></div>

<h2 class="abs section-title" style="top:1191px">BEST DEALS</h2>
<div class="abs deal deal-1" role="img" aria-label="Photo of a yellow villa with blue window frames beside a pool">
  <div class="deal-name">Villa Can Roig<br>Sabina</div>
  <div class="deal-btn teal" style="left:59px;top:354px">Book now</div>
</div>
<div class="abs deal deal-2" role="img" aria-label="Photo of a villa pool with loungers, parasol and red flowers">
  <div class="deal-name">Villa Les Tres Palmeres</div>
  <div class="deal-btn teal" style="left:155px;top:135px">Book now</div>
</div>
<div class="abs deal deal-3" role="img" aria-label="Photo of a villa terrace with pool, loungers and garden">
  <div class="deal-name">Villa Can Ferrer</div>
  <div class="deal-btn" style="left:89px;top:135px">Book now</div>
</div>
<div class="abs deal deal-4" role="img" aria-label="Photo of a rustic living room with sofas and wooden beams">
  <div class="deal-name">Agroturismo Can Marí</div>
  <div class="deal-btn" style="left:102px;top:162px">Book now</div>
</div>
<div class="abs deal deal-5" role="img" aria-label="Photo of a white villa with a round tower and palm garden">
  <div class="deal-name">Villa Can Ferrer</div>
  <div class="deal-btn" style="left:142px;top:162px">Book now</div>
</div>

<div class="abs testi-band"></div>
<h2 class="abs section-title" style="top:1732px">TESTIMONIALS</h2>
<div class="abs testi-card"></div>
<div class="abs avatar" role="img" aria-label="Portrait photo of the guest"></div>
<svg class="abs" style="left:356px;top:1916px" width="58" height="50" viewBox="0 0 58 50" aria-hidden="true">
  <path d="M26 4C12 6 2 14 2 28c0 10 6 18 13 18 6 0 10-4 10-10s-4-10-10-10c2-10 8-14 11-16z" fill="#dcdcdc"/>
  <path d="M56 4C42 6 32 14 32 28c0 10 6 18 13 18 6 0 10-4 10-10s-4-10-10-10c2-10 8-14 11-16z" fill="#dcdcdc"/>
</svg>
<svg class="abs" style="left:786px;top:1992px" width="58" height="50" viewBox="0 0 58 50" aria-hidden="true">
  <path d="M2 46c14-2 24-10 24-24C26 12 20 4 13 4 7 4 3 8 3 14s4 10 10 10c-2 10-8 14-11 16z" fill="#dcdcdc"/>
  <path d="M32 46c14-2 24-10 24-24C56 12 50 4 43 4c-6 0-10 4-10 10s4 10 10 10c-2 10-8 14-11 16z" fill="#dcdcdc"/>
</svg>
<p class="abs testi-text">Lorem ipsum dolor sit amet, consectetur adipiscing elit, sed do eiusmod tempor incididunt ut labore et dolore magna aliqua.</p>
<p class="abs testi-name">— Jane Doe</p>
<svg class="abs" style="left:254px;top:1926px" width="24" height="42" viewBox="0 0 24 42" aria-label="Previous"><path d="M22 1L2 21l20 20" fill="none" stroke="#8a8a8a" stroke-width="1.5"/></svg>
<svg class="abs" style="left:922px;top:1926px" width="24" height="42" viewBox="0 0 24 42" aria-label="Next"><path d="M2 1l20 20L2 41" fill="none" stroke="#8a8a8a" stroke-width="1.5"/></svg>

<footer class="abs footer" role="img" aria-label="Underwater photo of green posidonia seagrass meadow in blue sea"></footer>
<span class="foot-head" style="left:198px;top:2161px">ABOUT US</span>
<span class="foot-head" style="left:596px;top:2161px">CONTACT US</span>
<span class="foot-head" style="left:1007px;top:2161px">MENU</span>
<p class="abs foot-col" style="left:87px;top:2224px;width:275px"><strong>Amber and Slate Villas Ibiza</strong> is a company specialized in offering its clients accommodation in Villas on the countryside of Ibiza. Our guests enjoy the rural Ibiza, tranquility, relax, private pool, close to dream beaches and coves, the best restaurants, an unforgettable holiday for family or friends.</p>
<p class="abs foot-col" style="left:446px;top:2224px;width:306px;text-align:center;font-weight:600">Amber &amp; Slate Ibiza<br>CALLE DE LES PINEDES, 27,<br>SANTA EULARIA DES RIU, 07840,<br>IBIZA, Spain</p>
<p class="abs foot-col" style="left:420px;top:2313px;width:360px;text-align:center;font-weight:600">Email: reservas@amberandslatevillas.example</p>
<div class="abs foot-menu">HOME<br>EXPERIENCE<br>ABOUT US<br>CONTACT US<br>ALL PROPERTIES</div>

</body>
</html>
```